BVL - New Homepage needed for an existing website

Bright Valley Lantern Website
Need a new Homepage for an existing website with Action Items and Newer Pictures
This is the current Website
https://brightvalleylantern.example/

This new page will be changed on Jan 21st when Voting begins
1. Voting like a political campaign where we are trying to raise awareness for the issues we stand for and urge the people to go to a Polling /voting website and vote for us (Roster 4)
2. We have 6 basic themes as to what we stand for - there will be text to promote their importance of voting/call to action
3. There will be videos on the website and there will be a simulation of how the voting process works - will be added later

Use colors like the US Flag - Red, White and Blue. The other pages don't need to be changed - only the HomePage.

I only need the design, I will code the website. Thank you

Target Market(s)

Jewish People in the US

Industry/Entity Type

Religious

Number of Pages Required

1 page

Font styles to use
Serif
Sans Serif

Colors

Designer to choose colors to be used in the design.

Requirements
Must have
• Call to Action - Go out to Vote
• This is the current Website - https://brightvalleylantern.example/

```html
<!DOCTYPE html>
<html lang="en">
<head>
<meta charset="utf-8">
<title>Bright Valley Lantern – Home</title>
<link href="https://fonts.googleapis.com/css2?family=Montserrat:wght@800;900&family=Roboto:wght@400;500;700&display=swap" rel="stylesheet">
<style>
:root{
  --red:#a50021;
  --blue:#1a1a8c;
  --blue-deep:#2a2a9e;
  --ink:#222;
  --muted:#666;
  --white:#fff;
}
*{box-sizing:border-box;margin:0;padding:0}
html,body{width:1200px;height:3705px;overflow:hidden}
body{font-family:Roboto,Arial,sans-serif;color:var(--ink);background:var(--white);position:relative}
.abs{position:absolute}
.display{font-family:Montserrat,Arial,sans-serif;font-weight:900;text-transform:uppercase}
.display .hl{color:var(--red)}
.brand{left:112px;top:34px;display:flex;align-items:center;gap:8px;font-weight:700;font-size:15px;color:var(--red);width:150px;line-height:1.1}
.brand i{width:16px;height:16px;background:var(--red);flex:none}
.call{left:484px;top:22px;display:flex;align-items:center;gap:14px}
.call .bar{width:2px;height:64px;background:var(--red)}
.call small{display:block;font-size:11px;font-weight:700}
.call strong{display:block;font-size:23px;color:var(--blue);font-weight:700;letter-spacing:.5px}
.call em{display:block;font-style:normal;font-size:9px}
.btn{display:inline-flex;align-items:center;justify-content:center;border-radius:30px;font-weight:700;color:var(--white);text-transform:uppercase;white-space:nowrap}
.join-btn{left:858px;top:38px;width:230px;height:44px;background:var(--red);font-size:15px}
.nav{left:0;top:113px;width:1200px;height:45px;background:var(--blue);display:flex;padding-left:90px}
.nav a{color:var(--white);font-size:15px;font-weight:500;padding:0 21px;line-height:45px;text-decoration:none}
.nav a.on{background:var(--red)}
.hero{left:0;top:158px;width:1200px;height:532px;background:linear-gradient(90deg,#3a2418 0%,#5a3a2a 45%,#2a1d16 100%)}
.hero-text{left:112px;top:300px;color:var(--white)}
.hero-text .t1{font-size:32px;color:var(--blue-deep)}
.hero-text .t2{font-size:42px;margin-top:6px}
.hero-text p{font-size:18px;font-weight:500;margin-top:26px}
.hero-btn{left:112px;top:485px;width:375px;height:56px;background:var(--red);font-size:18px}
.arrow{width:36px;height:36px;border:2px solid var(--white);border-radius:50%}
.sec-title{width:1200px;left:0;text-align:center;font-size:34px;color:var(--blue)}
.card{width:304px;height:246px;background:var(--white);box-shadow:0 0 12px rgba(0,0,0,.1);padding:18px 20px}
.card svg{display:block;height:48px}
.card .rule{width:42px;height:3px;background:var(--red);margin:14px 0 12px}
.card h3{font-size:19px;font-weight:500;line-height:1.3}
.card p{font-size:13px;color:var(--muted);line-height:25px;margin-top:12px;text-align:justify}
.card .more{display:block;margin-top:10px;font-size:14px;font-weight:700;color:var(--blue)}
.video-band{left:0;top:1650px;width:1200px;height:740px}
.video{left:170px;top:1675px;width:860px;height:410px;border:4px solid var(--white);background:linear-gradient(90deg,#6b3a26,#2a1a14 50%,#4a2a20)}
.video .cap{left:90px;top:44px;color:var(--white);font-size:15px}
.video .tools{right:40px;top:28px;color:var(--white);font-size:15px;display:flex;gap:50px}
.play{left:396px;top:180px;width:64px;height:46px;background:#e00;border-radius:12px}
.quote{left:0;top:2260px;width:1200px;text-align:center;color:var(--white);font-size:17px;line-height:31px;font-weight:500}
.mission-img{left:30px;top:2500px;width:510px;height:445px;background:linear-gradient(135deg,#4aa3e0 0%,#9a9a9a 55%,#3d3d3d 100%);clip-path:polygon(50% 0,100% 30%,100% 100%,0 100%,0 30%)}
.mission{left:600px;top:2520px;width:488px}
.mission h2{font-size:32px;color:var(--blue)}
.mission h4{font-size:18px;font-weight:500;margin-top:10px}
.mission p{font-size:15px;color:var(--muted);line-height:27.5px;margin-top:26px;text-align:justify}
.mission .btn{margin-top:30px;width:150px;height:44px;background:var(--blue);font-size:15px}
.join{left:0;top:2945px;width:1200px;height:338px;background:var(--red);color:var(--white);text-align:center}
.join h2{margin-top:82px;font-size:33px}
.join p{font-size:15px;margin-top:18px}
.fields{display:flex;gap:20px;padding-left:112px;margin-top:32px}
.field{width:182px;height:43px;border-radius:22px;background:var(--white);color:#777;font-size:13px;text-align:left;padding:14px 20px}
.take{width:148px;height:43px;background:var(--blue);font-size:15px;margin-left:18px}
.footer{left:0;top:3283px;width:1200px;height:422px;background:#f4f4f6}
.fcol h5{font-size:19px;font-weight:500;color:var(--ink)}
.fcol p,.fcol li{font-size:14px;color:#666;line-height:26px;list-style:none}
.fcol p{margin-top:14px;width:270px}
.fcol ul{margin-top:10px;line-height:29px}
.fcol li::before{content:"» ";margin-right:8px}
.social{display:flex;gap:12px}
.social i{width:34px;height:34px;border-radius:50%;background:var(--blue)}
.social i:last-child{background:#e02a3a}
.copy{left:0;top:3658px;width:1200px;text-align:center;font-size:15px;color:#555}
</style>
</head>
<body>

<div class="abs brand"><i></i>Bright Valley Lantern</div>
<div class="abs call">
  <svg width="40" height="40" viewBox="0 0 40 40" fill="none" stroke="#1a1a8c" stroke-width="2.5"><path d="M8 6l7 8-4 4c2 5 6 9 11 11l4-4 8 7-4 5C16 35 5 24 3 10z"/></svg>
  <div class="bar"></div>
  <div><small>CALL US TODAY</small><strong>555-014-2026</strong><em>LIVE OPERATORS AVAILABLE - 7 DAYS A WEEK</em></div>
</div>
<div class="abs btn join-btn">Vote For Roster 4</div>

<nav class="abs nav">
  <a class="on">Home</a><a>Resist Assimilation</a><a>Confront Anti-Semitism</a><a>Expose BDS</a><a>Israel: The Eternal Jewish Homeland</a><a>View More ⌄</a>
</nav>

<div class="abs hero" role="img" aria-label="Photo of a woman praying in a pew inside a house of worship"></div>
<div class="abs hero-text">
  <div class="display t1">It's All About</div>
  <div class="display t2">Jewish <span class="hl">Continuity</span></div>
  <p>We Embrace Our Past To Ensure Our Future</p>
</div>
<div class="abs btn hero-btn">Go Out To Vote – Roster 4</div>
<div class="abs arrow" style="left:34px;top:406px"></div>
<div class="abs arrow" style="left:1126px;top:406px"></div>
<svg class="abs" style="left:0;top:690px" width="1200" height="60"><polygon points="0,0 600,0 0,60" fill="#a50021"/><polygon points="600,0 1200,0 1200,60" fill="#1a1a8c"/></svg>

<h2 class="abs display sec-title" style="top:852px">Our <span class="hl">Objectives</span></h2>

<div class="abs card" style="left:112px;top:942px">
  <svg viewBox="0 0 64 48" width="64" fill="none" stroke="#a50021" stroke-width="2"><rect x="4" y="4" width="14" height="10"/><rect x="24" y="2" width="14" height="10"/><rect x="44" y="4" width="14" height="10"/><circle cx="12" cy="28" r="4" stroke="#1a1a8c"/><circle cx="32" cy="28" r="4" stroke="#1a1a8c"/><circle cx="52" cy="28" r="4" stroke="#1a1a8c"/><path d="M4 44h56" stroke="#1a1a8c"/></svg>
  <div class="rule"></div><h3>Resist Assimilation</h3>
  <p>Assimilation is an issue facing every religion. With respect to Judaism, our movement underscores</p>
  <span class="more">DISCOVER MORE ➜</span>
</div>
<div class="abs card" style="left:449px;top:942px">
  <svg viewBox="0 0 56 48" width="56" fill="none" stroke="#1a1a8c" stroke-width="2"><path d="M28 0v48" stroke-dasharray="3 3"/><path d="M6 14h16M34 14h16" stroke="#a50021"/><path d="M10 46V30a8 8 0 0116 0M30 46V30a8 8 0 0116 0"/></svg>
  <div class="rule"></div><h3>Confront Anti-Semitism</h3>
  <p>Anti-Semitism in America unfortunately, becoming the new norm. While the attacks against Jews</p>
  <span class="more">DISCOVER MORE ➜</span>
</div>
<div class="abs card" style="left:785px;top:942px">
  <svg viewBox="0 0 40 48" width="40" fill="none" stroke="#1a1a8c" stroke-width="2"><rect x="2" y="2" width="36" height="44"/><path d="M12 16l8-8 8 8v6H12z" stroke="#a50021"/><path d="M10 30h20M10 36h20M10 42h20"/></svg>
  <div class="rule"></div><h3>Expose BDS</h3>
  <p>BDS has not yet gained enough traction to be a real threat currently, but the threat of BDS looms large when considering</p>
  <span class="more">DISCOVER MORE ➜</span>
</div>
<div class="abs card" style="left:112px;top:1228px">
  <svg viewBox="0 0 52 48" width="52" fill="none" stroke="#1a1a8c" stroke-width="2"><polygon points="26,2 48,38 4,38"/><polygon points="26,46 4,10 48,10" stroke="#a50021"/></svg>
  <div class="rule"></div><h3>Instill Jewish Pride</h3>
  <p>Due to the atmosphere on many if not most of our American college campuses, students are ashamed or scared</p>
  <span class="more">DISCOVER MORE ➜</span>
</div>
<div class="abs card" style="left:449px;top:1228px">
  <svg viewBox="0 0 52 48" width="52" fill="none" stroke="#1a1a8c" stroke-width="2"><path d="M4 46V26l14-12 14 12v20z"/><circle cx="36" cy="8" r="5" stroke="#a50021"/><circle cx="46" cy="8" r="5" stroke="#a50021"/></svg>
  <div class="rule"></div><h3>Israel: The Eternal Jewish Homeland</h3>
  <p>For thousands of years, Judaism has been inextricably bound with Israel.</p>
  <span class="more">DISCOVER MORE ➜</span>
</div>
<div class="abs card" style="left:785px;top:1228px">
  <svg viewBox="0 0 52 48" width="52" fill="none" stroke="#1a1a8c" stroke-width="2"><circle cx="26" cy="12" r="7" stroke="#a50021"/><circle cx="10" cy="32" r="5"/><circle cx="26" cy="32" r="5"/><circle cx="42" cy="32" r="5"/><path d="M2 46h48"/></svg>
  <div class="rule"></div><h3>Maintain Israel's Jewish Identity</h3>
  <p>While our movement recognizes that Jews are empowered with free</p>
  <span class="more">DISCOVER MORE ➜</span>
</div>

<h2 class="abs display sec-title" style="top:1590px">Our <span class="hl">Video</span></h2>

<svg class="abs video-band" viewBox="0 0 1200 740" preserveAspectRatio="none"><defs><linearGradient id="vb" x1="0" y1="0" x2="0" y2="1"><stop offset="0" stop-color="#2f2ba8"/><stop offset="1" stop-color="#26239a"/></linearGradient></defs><polygon points="0,0 170,25 1030,75 1200,100 1200,740 0,740" fill="url(#vb)"/></svg>
<div class="abs video" role="img" aria-label="Video still of children lighting candles on a menorah">
  <div class="abs cap">Rabbi D. Marlow · Bright Valley Lantern</div>
  <div class="abs tools"><span>Watch Later</span><span>Share</span></div>
  <div class="abs play"><svg width="64" height="46"><polygon points="26,14 42,23 26,32" fill="#fff"/></svg></div>
</div>
<h2 class="abs display sec-title" style="top:2200px;color:#fff">Bright Valley Lantern</h2>
<div class="abs quote">"By Connecting Jews To Their Heritage, History And Faith, We Can Ensure That Global<br>Jewry Not Only Survives, But Surges."</div>

<div class="abs mission-img" role="img" aria-label="Photo of a smiling woman giving a thumbs up in front of a blue star"></div>
<div class="abs mission">
  <h2 class="display">Bright Valley <span class="hl">Lantern</span></h2>
  <h4>MISSION STATEMENT</h4>
  <p>Bright Valley Lantern is a grassroots movement that was established to promote Jewish Continuity, recognizing that in the United States, Judaism and its continuity are under attack for a host of reasons, all of which Bright Valley Lantern believes must be identified, understood, and addressed in the appropriate manner.</p>
  <div class="btn">Read More ➜</div>
</div>

<div class="abs join">
  <h2 class="display">Go Out And Vote – Roster 4</h2>
  <p>Voting begins January 21st. Vote for Roster 4 to keep our people and communities strong, safe and proud.</p>
  <div class="fields">
    <div class="field">✎ Name</div><div class="field">✉ Email Address</div><div class="field">☏ Phone</div><div class="field">◉ City</div>
    <div class="btn take">Vote Now</div>
  </div>
</div>

<div class="abs footer"></div>
<div class="abs fcol" style="left:112px;top:3400px"><h5>Jewish Continuity</h5><p>Israel is the geographical anchor of Judaism, the Torah is the ideological/ theological anchor of Judaism</p></div>
<div class="abs fcol" style="left:455px;top:3400px"><h5>Quick Links</h5><ul><li>Home</li><li>Resist Assimilation</li><li>Confront Anti-Semitism</li><li>Expose BDS</li><li>View More</li></ul></div>
<div class="abs fcol" style="left:710px;top:3398px"><h5>Important</h5><ul><li>Terms of Use</li><li>Site Map</li><li>Privacy Policy</li><li>Disclaimer</li></ul></div>
<div class="abs brand" style="left:940px;top:3470px;width:130px">Bright Valley Lantern</div>
<div class="abs social" style="left:914px;top:3546px"><i></i><i></i><i></i><i></i></div>
<div class="abs copy">© 2020 Bright Valley Lantern. All Rights Reserved</div>

</body>
</html>
```